Quorva - corporate Business Card

We need a good look and innovative business card for a new start up company based in Los Angeles called "Quorva". We are in a payment business, including payment card, app, and ewallet. We are expert in online payment and Card not present (CNP) transaction.
We need an innovative, modern business card.

Our logo font is Aero Matics

Target Market(s)

Startup - Bank - Online Payment - Card Manufacturing

Industry/Entity Type

Startup

Contact Information for Business Card

phone: 555 014 7396 - Address: 4172 Marlowe blvd, Elmridge Park, OR 97299

Requirements
Must have
• Message: innovative, professional, expert, high tech, trust, online payment expert, security
Nice to have
• no comment
Should not have
• no Comment

```html
<!DOCTYPE html>
<html lang="en">
<head>
<meta charset="utf-8">
<title>Quorva – Business Card</title>
<link rel="stylesheet" href="https://fonts.googleapis.com/css2?family=Saira:wght@400;500;600;700&display=swap">
<style>
  :root {
    --brand-red: #b51d30;
    --ink: #1f1f1f;
    --card: #ffffff;
    --backdrop: #ece9e6;
    --card-shadow: rgba(0, 0, 0, 0.12);
  }
  * { margin: 0; padding: 0; box-sizing: border-box; }
  html, body {
    width: 1200px; height: 900px; overflow: hidden;
    background: var(--backdrop);
    font-family: "Saira", sans-serif;
  }
  .canvas { position: relative; width: 1200px; height: 900px; }

  .card {
    position: absolute;
    background: var(--card);
    border-radius: 22px;
    box-shadow: 0 6px 24px var(--card-shadow);
  }
  .card--front { left: 238px; top: 62px; width: 556px; height: 342px; }
  .card--back  { left: 458px; top: 518px; width: 558px; height: 344px; }

  .wordmark {
    position: absolute;
    color: var(--brand-red);
    font-weight: 600;
    text-transform: lowercase;
    letter-spacing: 1px;
    line-height: 1;
    white-space: nowrap;
  }
  .card--front .wordmark { left: 48px; top: 124px; font-size: 68px; }

  .divider {
    position: absolute; left: 316px; top: 93px;
    width: 1px; height: 158px; background: var(--brand-red);
  }

  .contact { position: absolute; left: 334px; top: 86px; color: var(--ink); white-space: nowrap; }
  .contact__name {
    color: var(--brand-red); font-weight: 700; font-size: 28px; line-height: 1.05;
  }
  .contact__title { font-size: 17px; line-height: 1.2; margin-bottom: 16px; }
  .contact__line { font-size: 15.5px; line-height: 23px; }
  .contact__label { color: var(--brand-red); font-weight: 600; margin-right: 8px; }
  .contact__address { font-size: 15.5px; line-height: 21px; margin-top: 14px; }

  .card--back .brand-dot {
    position: absolute; left: 117px; top: 124px;
  }
  .card--back .wordmark { left: 226px; top: 138px; font-size: 62px; }
</style>
</head>
<body>
<main class="canvas">
  <section class="card card--front" aria-label="Business card front">
    <div class="wordmark">Quorva</div>
    <div class="divider"></div>
    <div class="contact">
      <div class="contact__name">Daniel Reyes</div>
      <div class="contact__title">Director</div>
      <div class="contact__line"><span class="contact__label">M:</span>555 014 7396</div>
      <div class="contact__line"><span class="contact__label">W:</span>www.quorva.com</div>
      <div class="contact__address">4172 Marlowe blvd,<br>Elmridge Park, OR 97299</div>
    </div>
  </section>

  <section class="card card--back" aria-label="Business card back">
    <svg class="brand-dot" width="96" height="96" viewBox="0 0 96 96" aria-hidden="true">
      <circle cx="48" cy="48" r="48" fill="var(--brand-red)"/>
    </svg>
    <div class="wordmark">Quorva</div>
  </section>
</main>
</body>
</html>
```